Bramwell IT Services Business Card

Bramwell IT Services are a Perth based IT Services company. We would like to incorporate our company logo (attached) and stick with the blue that is in that design. I would like a clean look design that isn't too busy, yet creates a lasting image that is instantly recognisable in the recipients mind.

Target Market(s)

The target audience is small/medium business owners.

Industry/Entity Type

Business

Font styles to use
Serif
Sans Serif

Colors

Designer to choose colors to be used in the design.

Requirements
Must have
• The design should include:
Business name: Bramwell IT Services
Directors Name: Marcus Tenley
Phone Number: 0483 562 904
Email: support@bramwellit.com.au
Website: www.bramwellit.com.au

```html
<!DOCTYPE html>
<html lang="en">
<head>
<meta charset="utf-8">
<title>Bramwell IT Services – Business Card</title>
<link href="https://fonts.googleapis.com/css2?family=Open+Sans:wght@400;600&display=swap" rel="stylesheet">
<style>
  :root {
    --backdrop: #f4a7a4;
    --card-white: #ffffff;
    --brand-blue: #2a7cc7;
    --charcoal: #3f4144;
    --text-dark: #2e3033;
  }
  * { box-sizing: border-box; margin: 0; padding: 0; }
  html, body {
    width: 915px;
    height: 1200px;
    overflow: hidden;
    background: var(--backdrop);
    font-family: "Open Sans", Arial, sans-serif;
  }
  .sheet {
    position: relative;
    width: 915px;
    height: 1200px;
  }
  .card {
    position: absolute;
    left: 107px;
    width: 700px;
    height: 400px;
    background: var(--card-white);
    overflow: hidden;
    box-shadow: 0 14px 30px rgba(120, 40, 40, 0.25);
  }
  .card--front { top: 130px; }
  .card--back { top: 670px; }
  .card__shapes {
    position: absolute;
    inset: 0;
    width: 100%;
    height: 100%;
  }
  .shape--charcoal { fill: var(--charcoal); }
  .shape--blue { fill: var(--brand-blue); }

  .name-band {
    position: absolute;
    left: 34px;
    top: 70px;
    color: var(--card-white);
  }
  .name-band__name {
    font-size: 30px;
    font-weight: 400;
    line-height: 1.15;
  }
  .name-band__role {
    font-size: 19px;
    font-weight: 400;
    padding-left: 70px;
  }

  .wordmark {
    position: absolute;
    display: flex;
    align-items: center;
    gap: 10px;
    color: var(--brand-blue);
    font-weight: 600;
    white-space: nowrap;
  }
  .wordmark__square {
    background: var(--brand-blue);
    flex: none;
  }
  .card--front .wordmark {
    right: 34px;
    top: 54px;
    font-size: 22px;
  }
  .card--front .wordmark__square { width: 18px; height: 18px; }
  .card--back .wordmark {
    left: 50%;
    top: 50%;
    transform: translate(-50%, -50%);
    font-size: 36px;
  }
  .card--back .wordmark__square { width: 30px; height: 30px; }

  .contact {
    position: absolute;
    left: 120px;
    top: 200px;
    color: var(--text-dark);
    font-size: 16px;
    line-height: 1.75;
  }
  .contact__row { display: flex; }
  .contact__label { width: 72px; }
</style>
</head>
<body>
<main class="sheet">

  <section class="card card--front" aria-label="Business card front">
    <svg class="card__shapes" viewBox="0 0 700 400" aria-hidden="true">
      <polygon class="shape--charcoal" points="0,0 400,0 352,62 0,62"/>
      <polygon class="shape--blue" points="0,62 352,62 300,150 0,150"/>
      <polygon class="shape--blue" points="0,326 470,400 0,400"/>
      <polygon class="shape--charcoal" points="0,352 300,400 0,400"/>
      <polygon class="shape--blue" points="700,372 700,400 560,400"/>
    </svg>
    <div class="name-band">
      <p class="name-band__name">Marcus Tenley</p>
      <p class="name-band__role">Directors</p>
    </div>
    <div class="wordmark">
      <span class="wordmark__square"></span>
      <span class="wordmark__text">Bramwell IT Services</span>
    </div>
    <div class="contact">
      <p class="contact__row"><span class="contact__label">Phone</span><span>: 0483 562 904</span></p>
      <p class="contact__row"><span class="contact__label">Email</span><span>: support@bramwellit.com.au</span></p>
      <p class="contact__row"><span class="contact__label">Web</span><span>: www.bramwellit.com.au</span></p>
    </div>
  </section>

  <section class="card card--back" aria-label="Business card back">
    <svg class="card__shapes" viewBox="0 0 700 400" aria-hidden="true">
      <polygon class="shape--blue" points="470,0 700,0 700,130"/>
      <polygon class="shape--charcoal" points="530,0 700,0 700,96"/>
      <polygon class="shape--blue" points="0,300 250,400 0,400"/>
      <polygon class="shape--charcoal" points="0,330 175,400 0,400"/>
    </svg>
    <div class="wordmark">
      <span class="wordmark__square"></span>
      <span class="wordmark__text">Bramwell IT Services</span>
    </div>
  </section>

</main>
</body>
</html>
```